Modern card design needed for building development company

We are looking for a sharp modern new look for our business cards.
We are a New Zealand based company called TKR Ventures NZ LTD that specialises in subdividing large sections, housing and commercial buildings.
We have attached a photo of the current logo and would like to see it improved somehow as it looks a bit dated.
We are open to any colours.

Target Market(s)

Investors, Property buyers

Industry/Entity Type

Investment

Contact Information for Business Card

TKR VENTURES NZ LTD
www.tkrventuresnz.co.nz

Damon Whitcombe
Phone +64 21 938 104
Email dpwhitcombe@korumail.co.nz

Font styles to use
Serif
Sans Serif

Colors
0792cd
33a6d7
85cae6
6b449b
886aae
f04a50
ec1f27
f37122
f68d4d

Requirements
Must have
• Please try and make the logo more modern or if you have a similar one we would like to see it.

```html
<!DOCTYPE html>
<html lang="en">
<head>
<meta charset="utf-8">
<title>TKR Ventures NZ LTD – Business Card</title>
<link href="https://fonts.googleapis.com/css2?family=Source+Sans+3:wght@400;600&display=swap" rel="stylesheet">
<style>
  :root {
    --stage: #4a403b;
    --card: #121212;
    --card-edge: #1c1c1c;
    --ink-light: #e6e6e6;
    --ink-soft: #d2d2d2;
    --accent-blue: #1f5fd6;
    --accent-orange: #f37122;
    --text-font: "Source Sans 3", "Helvetica Neue", Arial, sans-serif;
  }
  * { box-sizing: border-box; margin: 0; padding: 0; }
  html, body {
    width: 1200px;
    height: 844px;
    overflow: hidden;
    background: var(--stage);
    font-family: var(--text-font);
  }
  .canvas {
    position: relative;
    width: 1200px;
    height: 844px;
  }
  .card {
    position: absolute;
    top: 273px;
    width: 520px;
    height: 298px;
    background: var(--card);
    border: 1px solid var(--card-edge);
    border-radius: 3px;
    box-shadow: 0 14px 30px rgba(0, 0, 0, 0.45);
  }
  .card--front { left: 50px; }
  .card--back { left: 630px; }

  .wordmark {
    display: flex;
    align-items: center;
    gap: 10px;
    color: var(--ink-light);
    font-weight: 600;
    letter-spacing: 0.06em;
    white-space: nowrap;
  }
  .wordmark__square {
    width: 16px;
    height: 16px;
    background: var(--accent-orange);
    flex: none;
  }
  .card--front .wordmark {
    position: absolute;
    top: 62px;
    right: 34px;
    font-size: 19px;
  }
  .card--back .wordmark {
    position: absolute;
    top: 50%;
    left: 50%;
    transform: translate(-50%, -50%);
    font-size: 24px;
  }

  .holder-name {
    position: absolute;
    left: 38px;
    bottom: 62px;
    color: var(--accent-blue);
    font-size: 21px;
    font-weight: 600;
  }

  .contact-list {
    position: absolute;
    right: 30px;
    top: 150px;
    list-style: none;
    text-align: right;
  }
  .contact-list__item {
    display: flex;
    justify-content: flex-end;
    align-items: center;
    gap: 8px;
    color: var(--ink-soft);
    font-size: 14px;
    line-height: 28px;
  }
  .contact-list__icon {
    width: 12px;
    height: 12px;
    flex: none;
  }
</style>
</head>
<body>
<main class="canvas">

  <section class="card card--front" aria-label="Business card front">
    <div class="wordmark">
      <span class="wordmark__square"></span>
      <span class="wordmark__name">TKR VENTURES NZ LTD</span>
    </div>

    <ul class="contact-list">
      <li class="contact-list__item">
        <span>+64 21 938 104</span>
        <svg class="contact-list__icon" viewBox="0 0 12 12" aria-hidden="true">
          <path d="M2.5 1 L4.5 1 L5.2 3.6 L3.9 4.6 Q5 7 7.4 8.1 L8.4 6.8 L11 7.5 L11 9.5 Q10.5 11 9 11 Q1 10 1 2.6 Q1 1.2 2.5 1 Z" fill="var(--accent-blue)"/>
        </svg>
      </li>
      <li class="contact-list__item">
        <span>dpwhitcombe@korumail.co.nz</span>
        <svg class="contact-list__icon" viewBox="0 0 12 12" aria-hidden="true">
          <rect x="0.5" y="2" width="11" height="8" rx="1" fill="var(--accent-blue)"/>
          <path d="M1 2.6 L6 6.6 L11 2.6" fill="none" stroke="var(--card)" stroke-width="1"/>
        </svg>
      </li>
      <li class="contact-list__item">
        <span>www.tkrventuresnz.co.nz</span>
        <svg class="contact-list__icon" viewBox="0 0 12 12" aria-hidden="true">
          <circle cx="6" cy="6" r="5.5" fill="var(--accent-blue)"/>
          <ellipse cx="6" cy="6" rx="2.3" ry="5.2" fill="none" stroke="var(--card)" stroke-width="0.8"/>
          <line x1="0.8" y1="6" x2="11.2" y2="6" stroke="var(--card)" stroke-width="0.8"/>
        </svg>
      </li>
    </ul>

    <p class="holder-name">Damon Whitcombe</p>
  </section>

  <section class="card card--back" aria-label="Business card back">
    <div class="wordmark">
      <span class="wordmark__square"></span>
      <span class="wordmark__name">TKR VENTURES NZ LTD</span>
    </div>
  </section>

</main>
</body>
</html>
```